Ridgeline Orchards Organic Cherry POS card 7x11

We are wanting to create a one-sided 7 x 11 organic cherry card that is eye catching and informative.This should be clear and easy to read and not cluttered. We use these cards as a display in grocery stores, demo stands, and other events to market Organic Ridgeline Sweet Orchards. We have a few facts that we would like displayed on the card (see attachment).

Target Market(s)

Consumers

Industry/Entity Type

Agriculture

Requirements
Must have
• Natural color palettes
• Easy to read
• Ridgeline Orchards
Nice to have
• Unique, realistic cherry design

```html
<!DOCTYPE html>
<html lang="en">
<head>
<meta charset="UTF-8">
<title>Ridgeline Orchards – Organic Cherry Card</title>
<link href="https://fonts.googleapis.com/css2?family=Lato:wght@400;700&family=Asap:wght@700&display=swap" rel="stylesheet">
<style>
  :root {
    --paper: #ffffff;
    --ink: #1b1b1b;
    --cherry: #8e1f2e;
    --band-dark: #0f7444;
    --band-mid: #1a9a5c;
    --band-light: #3fd79c;
    --band-edge: #0a4e2f;
    --backdrop-glow: #e0626a;
    --backdrop: #b0323f;
    --backdrop-deep: #8a1f2c;
    --fruit: #7a0f1c;
    --fruit-deep: #4a0810;
    --bowl: #1f4c52;
    --table: #2c4a52;
    --table-deep: #1d3238;
    --white: #ffffff;
  }
  * { margin: 0; padding: 0; box-sizing: border-box; }
  html, body { width: 764px; height: 1200px; overflow: hidden; background: var(--paper); }
  .card { position: relative; width: 764px; height: 1200px; background: var(--paper); font-family: "Lato", sans-serif; color: var(--ink); }

  .brand { position: absolute; top: 82px; left: 0; width: 100%; display: flex; justify-content: center; align-items: center; gap: 16px; }
  .brand-dot { width: 44px; height: 44px; border-radius: 50%; background: var(--cherry); }
  .brand-name { font-weight: 700; font-size: 44px; line-height: 52px; color: var(--ink); letter-spacing: 0.5px; }

  .fact-small { position: absolute; top: 207px; width: 100%; text-align: center; font-size: 15.5px; font-weight: 400; }
  .fact-headline { position: absolute; top: 242px; width: 100%; text-align: center; font-size: 20px; line-height: 31px; text-transform: uppercase; letter-spacing: 0.3px; }

  .photo { position: absolute; top: 326px; left: 0; width: 764px; height: 874px;
    background:
      radial-gradient(ellipse 300px 150px at 390px 580px, var(--fruit) 0%, rgba(122,15,28,0.85) 45%, transparent 100%),
      radial-gradient(ellipse 180px 90px at 390px 620px, var(--fruit-deep) 0%, transparent 100%),
      radial-gradient(ellipse 260px 120px at 390px 760px, var(--bowl) 0%, rgba(31,76,82,0.7) 55%, transparent 100%),
      radial-gradient(ellipse 380px 300px at 330px 110px, var(--backdrop-glow), transparent 72%),
      linear-gradient(180deg, var(--backdrop) 0%, var(--backdrop) 50%, var(--backdrop-deep) 75%, #5a2a32 79%, var(--table) 82%, var(--table-deep) 100%); }

  .band { position: absolute; top: 326px; left: 0; width: 764px; height: 46px;
    background: linear-gradient(90deg, var(--band-dark) 0%, var(--band-mid) 50%, var(--band-light) 100%);
    border-bottom: 2px solid var(--band-edge);
    display: flex; align-items: center; justify-content: center; }
  .band-title { color: var(--white); font-weight: 700; font-size: 34px; line-height: 46px; letter-spacing: 14.5px; margin-right: -14.5px; }

  .benefits { list-style: none; }
  .benefit { position: absolute; left: 0; height: 50px; width: 764px; }
  .benefit .tick { position: absolute; left: 62px; top: 12px; width: 28px; height: 28px; }
  .benefit .rule { position: absolute; left: 103px; top: 25px; height: 2px; background: var(--white); width: var(--rule); }
  .benefit .label { position: absolute; left: var(--text-x); top: 0; font-family: "Asap", sans-serif; font-weight: 700; font-size: 42px; line-height: 50px; color: var(--white); white-space: nowrap; letter-spacing: -0.3px; }
</style>
</head>
<body>
<main class="card">
  <header>
    <div class="brand">
      <span class="brand-dot" aria-hidden="true"></span>
      <span class="brand-name">Ridgeline Orchards</span>
    </div>
    <p class="fact-small">Organic Ridgeline cherries make up 1/3 of the nation’s production.</p>
    <p class="fact-headline">Washington State is the nation’s<br>largest producer of organic cherries.</p>
  </header>

  <div class="photo" role="img" aria-label="Photograph of a teal enamel bowl heaped with fresh dark red cherries with green stems, set on a weathered blue-grey wooden table with loose cherries, against a deep red textured backdrop"></div>

  <div class="band"><h2 class="band-title">HEALTH BENEFITS</h2></div>

  <ul class="benefits">
    <li class="benefit" style="top:404px; --rule:214px; --text-x:345px">
      <svg class="tick" viewBox="0 0 26 26"><rect x="1" y="4" width="20" height="20" fill="none" stroke="#fff" stroke-width="2"/><path d="M5 14 L10 20 L24 3" fill="none" stroke="#fff" stroke-width="4"/></svg>
      <span class="rule"></span><span class="label">Fat Free</span>
    </li>
    <li class="benefit" style="top:464px; --rule:107px; --text-x:226px">
      <svg class="tick" viewBox="0 0 26 26"><rect x="1" y="4" width="20" height="20" fill="none" stroke="#fff" stroke-width="2"/><path d="M5 14 L10 20 L24 3" fill="none" stroke="#fff" stroke-width="4"/></svg>
      <span class="rule"></span><span class="label">Source of VITAMIN C</span>
    </li>
    <li class="benefit" style="top:524px; --rule:24px; --text-x:147px">
      <svg class="tick" viewBox="0 0 26 26"><rect x="1" y="4" width="20" height="20" fill="none" stroke="#fff" stroke-width="2"/><path d="M5 14 L10 20 L24 3" fill="none" stroke="#fff" stroke-width="4"/></svg>
      <span class="rule"></span><span class="label">A Natural Anti-Inflammatory</span>
    </li>
    <li class="benefit" style="top:584px; --rule:94px; --text-x:216px">
      <svg class="tick" viewBox="0 0 26 26"><rect x="1" y="4" width="20" height="20" fill="none" stroke="#fff" stroke-width="2"/><path d="M5 14 L10 20 L24 3" fill="none" stroke="#fff" stroke-width="4"/></svg>
      <span class="rule"></span><span class="label">Source of POTASSIUM</span>
    </li>
    <li class="benefit" style="top:644px; --rule:100px; --text-x:216px">
      <svg class="tick" viewBox="0 0 26 26"><rect x="1" y="4" width="20" height="20" fill="none" stroke="#fff" stroke-width="2"/><path d="M5 14 L10 20 L24 3" fill="none" stroke="#fff" stroke-width="4"/></svg>
      <span class="rule"></span><span class="label">Source of MELATONIN</span>
    </li>
  </ul>
</main>
</body>
</html>
```